Alterations to existing business card

Here is my current logo and I want the "cafe and bar" taken off with just the words Lumo and our slogan "Savour every sip" on the card, Plus the logo.
Our Current Business Card is currently 5.5cm by 5.5cm and would like it to remain like this thanks.
The loyalty card can be 10 squares with the logo specifying the 10th coffee free. I would like the cheapest option please.
Also on our business card would like the Facebook logo and instagram Logo with TAZALUMO27 as link to our photos on instagram.

Keep Colour schemes the same please.

On the business cards

Dale Brinton Director
0427916038
dale27lumo@mailvista.test

Paula Ferrisi Principal
0428571963
paulumo@mailvista.test

Thanks Dale

Industry/Entity Type

Business

```html
<!DOCTYPE html>
<html lang="en">
<head>
<meta charset="utf-8">
<title>Lumo – Business &amp; Loyalty Cards</title>
<link rel="stylesheet" href="https://fonts.googleapis.com/css2?family=Open+Sans:wght@300;400;600;700&display=swap">
<style>
  :root {
    --backdrop: #e9e6e3;
    --ink: #111111;
    --card-black: #050505;
    --gold-deep: #e9a93a;
    --gold-mid: #f3c44c;
    --gold-light: #fbec88;
    --white: #ffffff;
  }
  * { box-sizing: border-box; margin: 0; padding: 0; }
  html, body {
    width: 1200px; height: 900px; overflow: hidden;
    background: var(--backdrop);
    font-family: "Open Sans", Arial, sans-serif;
  }
  .canvas { position: relative; width: 1200px; height: 900px; }

  /* Contact card */
  .contact-card {
    position: absolute; left: 248px; top: 70px; width: 326px; height: 326px;
    background: linear-gradient(135deg, var(--gold-deep) 0%, var(--gold-mid) 45%, var(--gold-light) 100%);
    border-top: 12px solid var(--card-black);
    border-bottom: 9px solid var(--card-black);
    color: var(--ink);
  }
  .brand-mark {
    position: absolute; left: 22px; top: 18px; width: 90px; height: 90px;
    border: 3px solid var(--ink); border-radius: 50%;
    display: flex; align-items: center; justify-content: center;
    font-weight: 600; font-size: 22px; color: var(--ink);
  }
  .social-links { position: absolute; right: 22px; top: 28px; display: flex; gap: 11px; }
  .social-dot { width: 32px; height: 32px; border-radius: 50%; background: var(--ink); }
  .people { position: absolute; right: 22px; top: 82px; text-align: right; }
  .person + .person { margin-top: 23px; }
  .person-name { font-weight: 700; font-size: 16px; line-height: 22px; }
  .person-role { font-size: 14px; line-height: 22px; margin-bottom: 7px; }
  .contact-line { font-size: 14px; line-height: 21px; display: flex; justify-content: flex-end; align-items: center; gap: 7px; }
  .contact-line svg { width: 11px; height: 11px; fill: var(--ink); }

  /* Loyalty card */
  .loyalty-card {
    position: absolute; left: 637px; top: 446px; width: 327px; height: 327px;
    background: var(--card-black);
    border-top: 13px solid var(--gold-mid);
    border-bottom: 10px solid var(--gold-mid);
    text-align: center;
  }
  .loyalty-ring {
    position: absolute; left: 119px; top: 16px; width: 88px; height: 88px;
    border: 3px solid var(--gold-mid); border-radius: 50%;
  }
  .loyalty-name {
    position: absolute; left: 0; right: 0; top: 116px;
    font-weight: 300; font-size: 30px; letter-spacing: 1px; color: var(--white); line-height: 34px;
  }
  .loyalty-slogan {
    position: absolute; left: 0; right: 0; top: 149px;
    font-size: 8px; line-height: 12px; letter-spacing: 1px; color: var(--gold-mid);
  }
  .stamp-grid {
    position: absolute; left: 39px; top: 193px;
    display: grid; grid-template-columns: repeat(5, 44px); column-gap: 7px; row-gap: 8px;
  }
  .stamp {
    width: 44px; height: 44px; border-radius: 50%;
    background: radial-gradient(circle at 40% 35%, var(--gold-light), var(--gold-mid) 55%, var(--gold-deep));
    display: flex; align-items: center; justify-content: center;
    font-weight: 600; font-size: 22px; color: var(--ink);
  }
  .stamp-free { background: var(--white); color: var(--gold-deep); font-size: 12px; font-weight: 700; }
</style>
</head>
<body>
<main class="canvas">
  <section class="contact-card" aria-label="Lumo business card">
    <div class="brand-mark">Lumo</div>
    <div class="social-links" aria-label="Social media">
      <span class="social-dot" aria-label="Photo sharing profile TAZALUMO27"></span>
      <span class="social-dot" aria-label="Social network page"></span>
    </div>
    <div class="people">
      <div class="person">
        <p class="person-name">Dale Brinton</p>
        <p class="person-role">Director</p>
        <p class="contact-line">0427916038
          <svg viewBox="0 0 24 24"><path d="M6.6 10.8a15 15 0 0 0 6.6 6.6l2.2-2.2a1 1 0 0 1 1-.25 11.4 11.4 0 0 0 3.6.57 1 1 0 0 1 1 1V20a1 1 0 0 1-1 1A17 17 0 0 1 3 4a1 1 0 0 1 1-1h3.5a1 1 0 0 1 1 1c0 1.25.2 2.45.57 3.57a1 1 0 0 1-.25 1z"/></svg></p>
        <p class="contact-line">dale27lumo@mailvista.test
          <svg viewBox="0 0 24 24"><path d="M2 5h20v2l-10 7L2 7z"/><path d="M2 9l10 7 10-7v10H2z"/></svg></p>
      </div>
      <div class="person">
        <p class="person-name">Paula Ferrisi</p>
        <p class="person-role">Principal</p>
        <p class="contact-line">0428571963
          <svg viewBox="0 0 24 24"><path d="M6.6 10.8a15 15 0 0 0 6.6 6.6l2.2-2.2a1 1 0 0 1 1-.25 11.4 11.4 0 0 0 3.6.57 1 1 0 0 1 1 1V20a1 1 0 0 1-1 1A17 17 0 0 1 3 4a1 1 0 0 1 1-1h3.5a1 1 0 0 1 1 1c0 1.25.2 2.45.57 3.57a1 1 0 0 1-.25 1z"/></svg></p>
        <p class="contact-line">paulumo@mailvista.test
          <svg viewBox="0 0 24 24"><path d="M2 5h20v2l-10 7L2 7z"/><path d="M2 9l10 7 10-7v10H2z"/></svg></p>
      </div>
    </div>
  </section>

  <section class="loyalty-card" aria-label="Lumo loyalty card">
    <div class="loyalty-ring"></div>
    <p class="loyalty-name">LUMO</p>
    <p class="loyalty-slogan">SAVOUR EVERY SIP</p>
    <div class="stamp-grid">
      <span class="stamp">1</span><span class="stamp">2</span><span class="stamp">3</span><span class="stamp">4</span><span class="stamp">5</span>
      <span class="stamp">6</span><span class="stamp">7</span><span class="stamp">8</span><span class="stamp">9</span><span class="stamp stamp-free">FREE</span>
    </div>
  </section>
</main>
</body>
</html>
```